Field Anchor - Design a new page for our website

The designer is to use our existing website to match color and style and the documents provided to create a webpage that reflects the information in the brochure attached. This should also include a button to download our brochure and a form to request more information by entering name, phone, and email. This page will be added to our main site and will be coded by our webmaster team.

View website at www.harrowfield.us

The successful designer will be asked to also design another page for additional compensation.

Target Market(s)

Security and Law Enforcement

Industry/Entity Type

Security Service

Coding

Number of Pages Required

1 page

Font styles to use
Other font styles liked:
• Raleway or match site font and style

Requirements
Must have
• Match in color and style to our existing site as this page will be added to the existing website.

UPDATE: Place FRB Logo (attached to the brief) in a horizontal bar the width of the page with the following text:

"Field Anchor and all of Harrowfield's services are available on under our FRB Contract." (Add button) Click for Info
Nice to have
• Simple design expressing clean and easy to comprehend points

Please be creative, use the ability to scroll vertically on the page to space out the content and add supporting graphics or images.

```html
<!DOCTYPE html>
<html lang="en">
<head>
<meta charset="utf-8">
<title>Harrowfield Consulting — Field Anchor</title>
<link href="https://fonts.googleapis.com/css2?family=Raleway:wght@300;400;500;600;700;800&display=swap" rel="stylesheet">
<style>
:root{
  --brand-blue:#2f8fde;
  --navy:#1f4e8a;
  --band-top:#2a58a3;
  --band-bottom:#1d3c78;
  --green:#2cbf5c;
  --red:#f50d0d;
  --salmon:#e8a08c;
  --ink:#333;
  --muted:#666;
  --card:#f6f6f6;
  --grey-bg:#f1f1f1;
  --title-blue:#1f5f9c;
  --orange:#e5592c;
}
*{box-sizing:border-box;margin:0;padding:0}
html,body{width:1200px;height:2500px;overflow:hidden}
body{font-family:"Raleway",sans-serif;color:var(--ink);background:#fff;position:relative}
.abs{position:absolute}

/* header + hero */
.hero{position:absolute;left:0;top:0;width:1200px;height:625px;
  background:linear-gradient(180deg,#5d6f86 0%,#4a5568 35%,#3b4250 70%,#2d3039 100%)}
.site-header{position:absolute;left:0;top:0;width:1200px;height:61px;background:rgba(60,110,170,.75)}
.brand{position:absolute;left:110px;top:12px;color:#fff;font-weight:700;font-size:28px;letter-spacing:.5px;display:flex;align-items:center;gap:8px}
.brand .dot{width:22px;height:22px;border-radius:50%;background:#fff}
.brand small{display:block;font-size:8px;letter-spacing:6px;font-weight:700;margin-top:-4px}
.main-nav{position:absolute;right:100px;top:17px;display:flex;align-items:center;gap:44px;font-size:11px;color:#fff}
.main-nav .contact{background:var(--red);padding:6px 15px;border-radius:2px}
.hero-title{position:absolute;left:0;top:203px;width:1200px;text-align:center;color:#fff;font-weight:400;font-size:38px;letter-spacing:.5px}
.hero-title span{color:var(--brand-blue);font-weight:600}
.lead{position:absolute;color:#fff;font-size:26px;font-weight:400}
.rotator{position:absolute;left:499px;top:266px;color:var(--salmon);font-weight:700;font-size:27px;line-height:28.5px}
.btn{position:absolute;display:flex;align-items:center;justify-content:center;color:#fff;font-weight:700;font-size:12.5px;letter-spacing:.2px}
.btn-red{background:var(--red)}
.btn-ghost{border:1px solid #fff}

/* cards */
.card{position:absolute;background:var(--card);box-shadow:0 1px 4px rgba(0,0,0,.15)}
.card-icon{position:absolute}
.card-title{position:absolute;font-weight:800;font-size:30px;line-height:26px}
.card-sub{position:absolute;font-size:20px;font-weight:400;color:#333}
.card-rule{position:absolute;height:1px;background:#ddd}
.card-body{position:absolute;font-size:12.6px;line-height:17.5px;color:#333}
.card-body p+p{margin-top:17px}
.card-bar{position:absolute;left:0;bottom:0;width:100%;height:4px}
.chev{position:absolute;width:30px;height:30px;border-radius:50%;display:flex;align-items:center;justify-content:center}

/* technologies */
.tech{position:absolute;left:0;top:1095px;width:1195px;height:437px;background:linear-gradient(180deg,var(--band-top),var(--band-bottom))}
.tech h2{position:absolute;left:0;top:27px;width:100%;text-align:center;font-size:32px;font-weight:400;color:#fff}
.tech h2 b{color:var(--salmon);font-weight:700}
.tech-grid{position:absolute;left:298px;top:110px;width:600px;height:290px;display:grid;grid-template-columns:repeat(3,1fr);grid-template-rows:1fr 1fr}
.tech-item{display:flex;flex-direction:column;align-items:center;justify-content:flex-end;padding-bottom:16px;color:#fff;font-weight:700;font-size:11px;text-align:center;line-height:12.5px;border-right:1px solid rgba(255,255,255,.07);border-bottom:1px solid rgba(255,255,255,.07)}
.tech-item:nth-child(3n){border-right:none}
.tech-item:nth-child(n+4){border-bottom:none}
.tech-item svg{margin-bottom:8px}

/* support */
.support-title{position:absolute;left:100px;top:1585px;font-size:32px;font-weight:700;color:#444}
.support-title b{color:var(--brand-blue)}
.acc-head{position:absolute;left:100px;width:350px;height:33px;color:#fff;font-size:20px;display:flex;align-items:center;padding-left:55px;gap:0}
.acc-head svg{position:absolute;right:20px}
.acc-body{position:absolute;left:100px;top:1676px;width:350px;height:106px;background:#fafafa;box-shadow:0 1px 3px rgba(0,0,0,.15);padding:14px 8px 0 10px;font-size:13px;line-height:19px;color:#666}
.media{position:absolute;left:537px;top:1597px;width:563px;height:437px;border-radius:6px;background:linear-gradient(135deg,#1d2630,#32404e 45%,#15191f)}

/* testimonials + contact */
.lower{position:absolute;left:0;top:2095px;width:1200px;height:355px;background:var(--grey-bg)}
.t-title{position:absolute;left:99px;top:2125px;font-size:26px;color:var(--title-blue);font-weight:400}
.t-sub{position:absolute;left:100px;top:2165px;font-size:13px;color:#444}
.quote{position:absolute;top:2225px;width:303px;height:115px;background:#e9e9e9;padding:14px 10px 0 25px;font-size:11.7px;line-height:19px;color:#777}
.quote svg{position:absolute;right:-2px;bottom:-8px}
.who{position:absolute;top:2350px;font-size:11px;color:var(--orange)}
.who small{display:block;font-size:8.5px;color:#888;margin-top:1px}
.divider{position:absolute;left:805px;top:2135px;width:1px;height:272px;background:#ddd}
.c-title{position:absolute;left:884px;top:2125px;font-size:26px;color:var(--title-blue)}
.c-title b{color:var(--brand-blue);font-weight:700}
.field{position:absolute;left:885px;width:215px;background:#fff;border:1px solid #e6e6e6;border-radius:2px;font-size:10px;color:#666;padding:9px 11px}
.send{position:absolute;left:885px;top:2362px;width:82px;height:27px;background:var(--red);color:#fff;font-weight:700;font-size:12px;display:flex;align-items:center;justify-content:center;border-radius:2px}

.site-footer{position:absolute;left:0;top:2450px;width:1200px;height:50px;background:#fff}
.site-footer p{position:absolute;left:0;top:27px;width:100%;text-align:center;font-size:8px;font-weight:700;color:#444;letter-spacing:.2px}
.site-footer .line{position:absolute;left:0;bottom:0;width:100%;height:4px;background:var(--brand-blue)}
</style>
</head>
<body>

<section class="hero" role="img" aria-label="Aerial photograph of a city skyline with glass towers, a river and highways at dusk"></section>

<header class="site-header">
  <div class="brand"><span class="dot"></span><div>Harrowfield<small>CONSULTING</small></div></div>
  <nav class="main-nav">
    <span>Home</span><span>About Us</span><span>Services</span><span>Core Markets</span><span>Blog</span><span class="contact">Contact Us</span>
  </nav>
</header>

<h1 class="hero-title">CREATING <span>SECURE</span> ENVIRONMENTS</h1>
<div class="lead" style="left:388px;top:267px">You can</div>
<div class="lead" style="left:668px;top:267px">the moment</div>
<div class="lead" style="left:388px;top:352px">You're in</div>
<div class="rotator">experience<br>be carefree<br>stay focused<br>control</div>
<a class="btn btn-red" style="left:317px;top:422px;width:291px;height:53px">DOWNLOAD OUR BROCHURE</a>
<a class="btn btn-ghost" style="left:621px;top:422px;width:262px;height:53px">SCHEDULE A FREE CONSULTATION</a>

<!-- special events card -->
<article class="card" style="left:100px;top:683px;width:496px;height:222px">
  <svg class="card-icon" style="left:19px;top:30px" width="80" height="82" viewBox="0 0 80 82" fill="none" stroke="#1f4e8a" stroke-width="4">
    <rect x="3" y="10" width="74" height="68" rx="4"/><line x1="3" y1="27" x2="77" y2="27"/>
    <rect x="17" y="2" width="8" height="16" rx="2"/><rect x="55" y="2" width="8" height="16" rx="2"/>
    <path d="M40 36l5 11 12 1-9 8 3 12-11-7-11 7 3-12-9-8 12-1z" stroke-linejoin="round"/>
  </svg>
  <div class="card-title" style="left:112px;top:45px;color:var(--brand-blue)">SPECIAL EVENTS</div>
  <div class="card-sub" style="left:112px;top:77px">Pose Special Challenges</div>
  <div class="card-rule" style="left:112px;top:108px;width:355px"></div>
  <div class="card-body" style="left:19px;top:123px;width:465px">Managing security is stressful under the best of circumstances – planning for both the expectedand unexpected is part of the job. But when you're tasked with securing a special event, emergency or disaster recovery, the "unexpected"<br><b style="font-size:8px">READ MORE.</b></div>
  <div class="card-bar" style="background:var(--brand-blue)"></div>
  <div class="chev" style="left:233px;bottom:-13px;background:var(--brand-blue)"><svg width="14" height="9" viewBox="0 0 14 9"><path d="M1 1l6 6 6-6" stroke="#fff" stroke-width="2" fill="none"/></svg></div>
</article>

<!-- field anchor card -->
<article class="card" style="left:603px;top:683px;width:497px;height:350px">
  <svg class="card-icon" style="left:18px;top:26px" width="96" height="86" viewBox="0 0 96 86" fill="none" stroke="#2cbf5c" stroke-width="4">
    <path d="M38 14a18 18 0 0 1 22 0M42 20a10 10 0 0 1 14 0"/><circle cx="49" cy="26" r="2.5" fill="#2cbf5c"/>
    <path d="M3 34h62l8 14h18v22H3z" stroke-linejoin="round"/>
    <rect x="12" y="42" width="14" height="12"/><rect x="32" y="42" width="14" height="12"/>
    <circle cx="20" cy="74" r="7" fill="#f6f6f6"/><circle cx="74" cy="74" r="7" fill="#f6f6f6"/>
  </svg>
  <div class="card-title" style="left:128px;top:23px;color:var(--green)">HARROWFIELD'S FIELD<br>ANCHOR</div>
  <div class="card-sub" style="left:128px;top:80px">Special Event Services</div>
  <div class="card-rule" style="left:128px;top:110px;width:357px"></div>
  <div class="card-body" style="left:20px;top:124px;width:465px">
    <p>Harrowfield's Field Anchor and Special Event Services provides your special &nbsp;event with the same levelof technology and resources you'd expect at a permanent installation. With a comprehensive, highly reliableand redundant</p>
    <p>&nbsp;set of surveillance, monitoring and communication systems at your disposal, our state-of-theart field anchor center is equipped with everything you need to execute a successful event.</p>
    <p>All systemsare managed and monitored from within our Command Vehicle, furnished with large screen monitors and arobust software platform that rivals traditional Security Operations Centers</p>
  </div>
  <div class="card-bar" style="background:var(--green)"></div>
  <div class="chev" style="left:249px;top:333px;background:var(--green)"><svg width="14" height="9" viewBox="0 0 14 9"><path d="M1 8l6-6 6 6" stroke="#fff" stroke-width="2" fill="none"/></svg></div>
</article>

<!-- technologies -->
<section class="tech">
  <h2><b>SECURITY</b> Technologies</h2>
  <div class="tech-grid">
    <div class="tech-item">
      <svg width="76" height="62" viewBox="0 0 76 62" fill="#fff"><rect x="4" y="8" width="66" height="16" rx="3"/><path d="M10 26h56c0 18-12 32-28 32S10 44 10 26z"/><circle cx="38" cy="42" r="7" fill="#24498e"/><circle cx="64" cy="14" r="3" fill="#24498e"/><path d="M58 6a9 9 0 0 1 12 0" stroke="#fff" stroke-width="2" fill="none"/></svg>
      RAPID VIDEO SYSTEM<br>DEPLOYMENT
    </div>
    <div class="tech-item">
      <svg width="100" height="76" viewBox="0 0 100 76" fill="none" stroke="#fff" stroke-width="3"><path d="M40 10a14 14 0 0 1 20 0M44 16a7 7 0 0 1 12 0"/><ellipse cx="50" cy="46" rx="18" ry="14" fill="#fff"/><path d="M4 38h28M68 38h28M14 34v10M86 34v10M38 58l-4 14M62 58l4 14"/></svg>
      AERIAL DRONE<br>SURVEILLANCE
    </div>
    <div class="tech-item">
      <svg width="72" height="72" viewBox="0 0 72 72" fill="none" stroke="#fff" stroke-width="3"><circle cx="36" cy="36" r="34" fill="#fff"/><circle cx="36" cy="36" r="26" stroke="#2a56a0"/><circle cx="36" cy="36" r="16" stroke="#2a56a0"/><circle cx="36" cy="36" r="5" stroke="#2a56a0"/><path d="M36 36L20 14" stroke="#2a56a0"/></svg>
      DRONE DETECTION<br>TECHNOLOGY
    </div>
    <div class="tech-item">
      <svg width="72" height="72" viewBox="0 0 72 72" fill="none" stroke="#fff" stroke-width="4"><circle cx="36" cy="36" r="32"/><path d="M14 14l44 44"/><path d="M20 30h30l6 6h-8v10h-8l-4-6H20z" fill="#fff" stroke-width="2"/></svg>
      GUNFIRE DETECTION
    </div>
    <div class="tech-item">
      <svg width="82" height="82" viewBox="0 0 82 82" fill="none" stroke="#fff" stroke-width="4" stroke-linecap="round"><path d="M41 4v74M41 14l-7-6M41 14l7-6M41 68l-7 6M41 68l7 6M41 41l30-17M41 41l30 17M62 20l2 9M62 62l2-9"/><path d="M36 22a19 19 0 0 0 0 38z" fill="#fff"/><path d="M6 41h8M12 20l6 6M12 62l6-6M22 8l3 7M22 74l3-7"/></svg>
      REAL-TIME WEATHER<br>MONITORING
    </div>
    <div class="tech-item">
      <svg width="84" height="74" viewBox="0 0 84 74" fill="none" stroke="#fff" stroke-width="4"><rect x="2" y="2" width="80" height="54" rx="3"/><path d="M42 56v10M26 70h32"/><rect x="14" y="12" width="24" height="28" fill="#fff"/><circle cx="26" cy="22" r="4" stroke="#24498e" stroke-width="2"/><path d="M46 16h24M46 26h24M46 36h24"/></svg>
      SOCIAL MEDIA<br>MONITORING
    </div>
  </div>
</section>

<!-- support -->
<h2 class="support-title"><b>SUPPORT</b> Services</h2>
<div class="acc-head" style="top:1643px;background:var(--brand-blue)">Professional Technical Staff<svg width="14" height="9" viewBox="0 0 14 9"><path d="M1 1l6 6 6-6" stroke="#fff" stroke-width="2" fill="none"/></svg></div>
<div class="acc-body">Our highly knowledgeable technical staff ensures that the technology aboard the field anchor is expressly programmed and deployed for each event to maximize its effectiveness.</div>
<div class="acc-head" style="top:1795px;background:var(--green);padding-left:18px">Seasoned Security Professionals<svg width="14" height="9" viewBox="0 0 14 9"><path d="M1 1l6 6 6-6" stroke="#fff" stroke-width="2" fill="none"/></svg></div>
<a class="btn btn-red" style="left:100px;top:1980px;width:292px;height:53px">DOWNLOAD OUR BROCHURE</a>
<div class="media" role="img" aria-label="Screenshot of video editing software showing a city street with flags and audio waveforms"></div>

<!-- testimonials + contact -->
<section class="lower"></section>
<h2 class="t-title">Testimonials</h2>
<p class="t-sub">We help people with real solutions. Here's what they think about our service:</p>
<blockquote class="quote" style="left:100px">Lorem ipsum dolor sit amet, consectetur adipiscing elit, sed do eiusmod tempor incididunt ut labore et dolore magna aliqua. Quis ipsum suspendisse ultrices gravida. Risus commodo viverra maecenas accumsan lacus vel facilisis.<svg width="22" height="22" viewBox="0 0 22 22"><path d="M0 2h22L10 22z" fill="var(--orange)"/></svg></blockquote>
<blockquote class="quote" style="left:424px">Lorem ipsum dolor sit amet, consectetur adipiscing elit, sed do eiusmod tempor incididunt ut labore et dolore magna aliqua. Quis ipsum suspendisse ultrices gravida. Risus commodo viverra maecenas accumsan lacus vel facilisis.<svg width="22" height="22" viewBox="0 0 22 22"><path d="M0 2h22L10 22z" fill="var(--orange)"/></svg></blockquote>
<div class="who" style="left:100px">Dana Whitlock<small>Global Strategy and Architecture</small></div>
<div class="who" style="left:424px">Dana Whitlock<small>Global Strategy and Architecture</small></div>
<div class="divider"></div>

<h2 class="c-title">Contact <b>Us</b></h2>
<div class="field" style="top:2165px;height:29px">Your name</div>
<div class="field" style="top:2201px;height:29px">Email</div>
<div class="field" style="top:2236px;height:29px">Phone number</div>
<div class="field" style="top:2271px;height:82px">Ask something . . .</div>
<a class="send">SEND</a>

<footer class="site-footer">
  <p>PRIVACY POLICY |© 2020 HARROWFIELD CONSULTING. ALL RIGHTS RESERVED. WEB DESIGN BY BRIGHTLOOM STUDIO.</p>
  <div class="line"></div>
</footer>

</body>
</html>
```